Banner for construction site to identify developer

we need a 4 foot by 8 foot banner to hang on the fence of a residential townhome development in Phoenix, Arizona that identifies Tolvane Holdings as the company behind the development/project. Also needs to include the logo, phone number, and web address. Would like to stick with the blue colors provided in the attached logo. The blues should stay the same but the letters in the logo can change to another color if necessary. Feel free to use "Tolvane Holdings" in place of "Tolvane Holdings Group". Looking for use of colors/design to take up space so banner is not just text with a logo.

Target Market(s)

drive by traffic looking at the site

Industry/Entity Type

Real Estate

Colors
0054AA
0677BA
7BADD7
CADEEF
E8F1F8

Requirements
Must have
• company name, phone number and web address

```html
<!DOCTYPE html>
<html lang="en">
<head>
<meta charset="utf-8">
<title>Tolvane Holdings – Site Banner</title>
<link href="https://fonts.googleapis.com/css2?family=Source+Sans+3:wght@400;600;700&display=swap" rel="stylesheet">
<style>
  :root {
    --backdrop: #a9a9a9;
    --banner-white: #ffffff;
    --brand-blue: #1f6fa0;
    --brand-blue-bright: #21a3d8;
    --charcoal: #414042;
    --name-ink: #3d3d3f;
    --text-light: #ffffff;
  }
  html, body {
    margin: 0;
    padding: 0;
    width: 921px;
    height: 1200px;
    overflow: hidden;
    background: var(--backdrop);
    font-family: "Source Sans 3", "Myriad Pro", Arial, sans-serif;
  }
  .canvas {
    position: relative;
    width: 921px;
    height: 1200px;
  }
  .banner {
    position: absolute;
    left: 30px;
    top: 385px;
    width: 861px;
    height: 430px;
    background: var(--banner-white);
    box-shadow: 0 10px 22px rgba(0, 0, 0, 0.35);
    display: flex;
    flex-direction: column;
  }
  .banner__identity {
    height: 233px;
    display: flex;
    align-items: flex-end;
    justify-content: center;
    gap: 20px;
    padding-bottom: 38px;
    box-sizing: border-box;
  }
  .identity__mark {
    width: 34px;
    height: 34px;
    background: var(--brand-blue-bright);
    margin-bottom: 14px;
  }
  .identity__name {
    margin: 0;
    font-size: 70px;
    font-weight: 700;
    letter-spacing: -1.5px;
    line-height: 1;
    color: var(--name-ink);
  }
  .banner__phone {
    height: 97px;
    background: var(--brand-blue);
    display: flex;
    align-items: center;
    justify-content: center;
    gap: 22px;
    color: var(--text-light);
  }
  .phone__icon {
    width: 44px;
    height: 44px;
  }
  .phone__number {
    font-size: 70px;
    font-weight: 700;
    letter-spacing: 0.5px;
    line-height: 1;
  }
  .banner__divider {
    height: 3px;
    background: var(--banner-white);
  }
  .banner__web {
    flex: 1;
    background: var(--charcoal);
    display: flex;
    align-items: center;
    justify-content: center;
    color: var(--text-light);
    font-size: 40px;
    letter-spacing: 1.5px;
    font-weight: 400;
  }
  .web__domain {
    font-weight: 700;
  }
</style>
</head>
<body>
  <main class="canvas">
    <section class="banner" aria-label="Tolvane Holdings site banner">
      <header class="banner__identity">
        <span class="identity__mark" aria-hidden="true"></span>
        <h1 class="identity__name">Tolvane Holdings</h1>
      </header>
      <div class="banner__phone">
        <svg class="phone__icon" viewBox="0 0 44 44" aria-hidden="true">
          <circle cx="22" cy="22" r="22" fill="#ffffff"/>
          <path d="M14.5 12.5c1-1 2.4-.9 3.1.2l2.2 3.3c.6.9.4 2-.4 2.7l-1.3 1.1c1 2.4 2.9 4.4 5.3 5.5l1.2-1.3c.7-.8 1.9-.9 2.7-.3l3.3 2.2c1.1.7 1.2 2.2.2 3.1l-1.6 1.6c-1.2 1.2-3 1.5-4.5.8-5.3-2.4-9.5-6.6-11.9-11.9-.7-1.5-.4-3.3.8-4.5z" fill="#1f6fa0"/>
          <path d="M24 11.5a9 9 0 0 1 8.5 8.5M24 15.5a5 5 0 0 1 4.5 4.5" fill="none" stroke="#1f6fa0" stroke-width="2" stroke-linecap="round"/>
        </svg>
        <span class="phone__number">(480) 555-0147</span>
      </div>
      <div class="banner__divider"></div>
      <footer class="banner__web">
        <span>www.<span class="web__domain">tolvaneholdingsgroup</span>.com</span>
      </footer>
    </section>
  </main>
</body>
</html>
```